Velmarsh Group Webpage Design

We need a new website for our company. The company is Velmarsh Group Pty Ltd. We are in the business of Asbestos Removal; Demolition; Earthworks and Transport. We do not advertise and would like our website to be a reference point for our clients / potential clients and also to make our services known to those searching the internet for the services we offer. Some examples of the style of website we are after are:
http://www.quarnedemolition-example.com.au/
http://m.brintowerdemolitions-example.com.au/
http://www.fenwarddemolition-example.com.au
http://www.tolvik-example.com.au
http://www.ptrservices-example.com.au
http://www.steadfast-dismantling-example.com.au
We will need to work on content. Enclosed is an example. We also need to purchase the domain velmarshgroup-example.com.au and need to set up email accounts and ensure the website is mobile friendly. We have a company logo and have built our business on delivering professional, quality services on time. We would like the webpage to be simple, informative and professional - black and white / grey themed. We would also like to add a photo gallery etc later.

Industry/Entity Type

Construction

Coding

Coded - Design and coding required

Number of Pages Required

1 page

Colors
000000
fcfcfc
959595
dddddd

Requirements
Must have
• Information regarding the services we provide

```html
<!DOCTYPE html>
<html lang="en">
<head>
<meta charset="utf-8">
<title>Velmarsh Group</title>
<link href="https://fonts.googleapis.com/css2?family=Open+Sans:wght@400;600;700&display=swap" rel="stylesheet">
<style>
:root{
  --accent:#ae5e55;
  --ink:#1a1a1a;
  --body:#555555;
  --soft:#f6f6f6;
  --white:#ffffff;
  --footer:#1c1c1c;
  --footer-text:#8a8a8a;
  --footer-line:#333333;
  --icon:#111111;
}
*{margin:0;padding:0;box-sizing:border-box}
html,body{width:1200px;height:2228px;overflow:hidden;background:var(--white)}
body{font-family:"Open Sans",Arial,sans-serif;color:var(--body);position:relative}
.site-header{position:absolute;left:0;top:0;width:1200px;height:96px;background:var(--white)}
.brand{position:absolute;left:98px;top:26px;font-size:34px;font-weight:400;letter-spacing:4px;color:var(--accent)}
.main-nav{position:absolute;right:98px;top:32px;display:flex;gap:34px;font-size:15px;color:#333}
.main-nav a{color:inherit;text-decoration:none;position:relative;padding:0 4px}
.main-nav a.active{color:var(--accent)}
.main-nav a.active::after{content:"";position:absolute;left:-16px;right:-16px;top:28px;height:1px;background:var(--accent)}
.hero{position:absolute;left:0;top:96px;width:1200px;height:532px;background:linear-gradient(180deg,#c9d6e3 0%,#aebccb 38%,#8d8a80 62%,#6f6456 100%)}
.hero-arrow{position:absolute;top:258px;width:28px;height:28px;border-radius:50%;background:rgba(60,60,60,.6)}
.hero-arrow.prev{left:12px}.hero-arrow.next{right:12px}
.hero-caption{position:absolute;left:0;right:0;top:438px;display:flex;justify-content:center;gap:10px;align-items:center}
.hero-caption span{background:rgba(20,20,20,.75);color:var(--white);font-weight:700;font-size:32px;padding:2px 10px}
.hero-caption i{color:var(--white);font-style:normal;font-weight:700;font-size:32px}
.section{position:absolute;left:0;width:1200px}
.section-title{text-align:center;font-size:26px;font-weight:600;color:var(--ink)}
.divider{display:block;margin:6px auto 0;width:128px;height:12px}
.lead{width:1004px;margin:22px auto 0;font-size:12.5px;line-height:20px;text-align:center;color:var(--body)}
.about{top:628px;height:208px;background:var(--soft);padding-top:34px}
.services{top:836px;height:456px;padding-top:32px}
.service-grid{position:absolute;left:98px;top:180px;width:1004px;display:flex;justify-content:space-between}
.service-card{width:320px;text-align:center}
.service-card svg{height:60px}
.service-card h3{font-size:21px;font-weight:400;color:var(--ink);margin-top:10px}
.service-card p{font-size:12.5px;line-height:19px;text-align:justify;text-align-last:center;margin-top:10px}
.hours{top:1292px;height:200px;background:var(--accent);color:var(--white);padding-top:28px}
.hours .section-title{color:var(--white)}
.hours .lead{color:var(--white);font-size:16px;line-height:27px;width:960px}
.safety{top:1492px;height:468px;padding-top:42px}
.safety-photo{position:absolute;left:98px;top:136px;width:385px;height:252px;background:linear-gradient(135deg,#e9eef6 0%,#a9bfdc 50%,#1f4e9a 100%)}
.safety-copy{position:absolute;left:532px;top:128px;width:570px;font-size:13px;line-height:24px;color:var(--ink)}
.safety-copy ul{list-style:none;margin-top:16px}
.safety-copy li{position:relative;padding-left:30px}
.safety-copy li::before{content:"•";position:absolute;left:0}
.site-footer{position:absolute;left:0;top:1960px;width:1200px;height:268px;background:var(--footer);color:var(--footer-text)}
.contact-row{position:absolute;left:98px;top:40px;width:1004px;display:flex}
.contact-item{flex:1;text-align:center;font-size:11.5px;line-height:19px;height:80px;padding-top:0}
.contact-item+.contact-item{border-left:1px solid var(--footer-line)}
.contact-item svg{display:block;margin:0 auto 12px}
.social{position:absolute;left:0;right:0;top:166px;display:flex;justify-content:center;gap:10px}
.social span{width:28px;height:28px;border-radius:50%;background:#3e3e3e}
.social span.on{background:#3aa9e0}
.copyright{position:absolute;left:0;right:0;top:214px;text-align:center;font-size:10.5px;letter-spacing:1px}
</style>
</head>
<body>
<header class="site-header">
  <div class="brand">VELMARSH GROUP</div>
  <nav class="main-nav">
    <a class="active">Home</a><a>About Us</a><a>Services</a><a>Gallery</a><a>Projects</a><a>Contact Us</a>
  </nav>
</header>

<section class="hero" role="img" aria-label="Photo of cranes and excavators on a harbourside construction site with city towers behind">
  <span class="hero-arrow prev"></span><span class="hero-arrow next"></span>
  <div class="hero-caption"><span>Transport</span><i>.</i><span>Demolition</span><i>.</i><span>Earthmoving</span><i>.</i></div>
</section>

<section class="section about">
  <h2 class="section-title">About Us</h2>
  <svg class="divider" viewBox="0 0 128 12"><path d="M0 10H56L64 3L72 10H128" fill="none" stroke="#ae5e55" stroke-width="1.5"/></svg>
  <p class="lead">Velmarsh Transport Pty Ltd was established by Director Daniel Velmarsh in 2002 with a focus providing services within the transport industry. Over time the company has developed and expanded to include the provision of Earthworks and Demolition. Daniel has over 10 years’ experience working at all levels within these industries focusing primarily on Demolition and Earthworks in recent times. Velmarsh Transport and Demolition is built on core values of Service, Safety and Environment and are dedicated to delivering a quality, safe, cost effective, efficient and reliable service.</p>
</section>

<section class="section services">
  <h2 class="section-title">Service</h2>
  <svg class="divider" viewBox="0 0 128 12"><path d="M0 10H56L64 3L72 10H128" fill="none" stroke="#ae5e55" stroke-width="1.5"/></svg>
  <p class="lead">Velmarsh Transport and Demolition offer an extensive range of services including Demolition, Earthworks and Asbestos Removal. We make it our business to consult with clients, assess their needs and tailor a complete solution. We pride ourselves on a professional approach and timely delivery of services.</p>
  <div class="service-grid">
    <div class="service-card">
      <svg viewBox="0 0 70 60" width="70"><circle cx="20" cy="40" r="16" fill="#111"/><line x1="20" y1="24" x2="16" y2="2" stroke="#111" stroke-width="2"/><g fill="#111"><rect x="42" y="18" width="12" height="7"/><rect x="56" y="18" width="12" height="7"/><rect x="40" y="28" width="12" height="7"/><rect x="54" y="28" width="12" height="7"/><rect x="42" y="38" width="12" height="7"/><rect x="56" y="38" width="12" height="7"/><rect x="40" y="48" width="12" height="7"/><rect x="54" y="48" width="12" height="7"/></g></svg>
      <h3>Demolition</h3>
      <p>Velmarsh Transport and Demolition provide an extensive range of demolition services. A large amount of experience across a broad range of projects results in a dependable service and peace of mind for all clients. Services include:</p>
    </div>
    <div class="service-card">
      <svg viewBox="0 0 100 60" width="100"><g fill="#111"><rect x="40" y="30" width="40" height="14"/><rect x="62" y="20" width="16" height="12"/><rect x="36" y="46" width="50" height="10" rx="5"/><path d="M44 32L22 12L6 40L14 42L24 24L40 38Z"/><path d="M2 40H18L14 52H4Z"/></g></svg>
      <h3>Earthworks</h3>
      <p>Velmarsh Transport and Demolition possess all necessary equipment and skilled personnel to provide earthmoving services including:</p>
    </div>
    <div class="service-card">
      <svg viewBox="0 0 60 60" width="60"><path d="M30 8L56 54H4Z" fill="none" stroke="#111" stroke-width="5" stroke-linejoin="round"/><rect x="28" y="24" width="4" height="17" fill="#111"/><rect x="28" y="44" width="4" height="4" fill="#111"/></svg>
      <h3>Asbestos</h3>
      <p>Asbestos is a naturally occurring silicate mineral made up of tiny fibres. When disturbed, it may produce a dust containing asbestos fibres. Breathing these fibres into the lungs may, in turn, cause a range of health problems including pleural plaques, asbestosis, lung cancer and mesothelioma.</p>
    </div>
  </div>
</section>

<section class="section hours">
  <h2 class="section-title">Hours of Operation</h2>
  <svg class="divider" viewBox="0 0 128 12"><path d="M0 10H56L64 3L72 10H128" fill="none" stroke="#ffffff" stroke-width="1.5"/></svg>
  <p class="lead">Velmarsh Transport and Demolition operate Monday to Saturday. Hours of operation are generally assessed and implemented to meet the needs of each individual project.</p>
</section>

<section class="section safety">
  <h2 class="section-title">Safety</h2>
  <svg class="divider" viewBox="0 0 128 12"><path d="M0 10H56L64 3L72 10H128" fill="none" stroke="#ae5e55" stroke-width="1.5"/></svg>
  <div class="safety-photo" role="img" aria-label="Photo of safety goggles resting on a health and safety folder"></div>
  <div class="safety-copy">
    <p>The safety of our clients, workforce and wider community is of paramount importance to Velmarsh Transport and Demolition. We employ a comprehensive Safety Management System ensuring:</p>
    <ul>
      <li>A safe work environment</li>
      <li>Safe plant and structures</li>
      <li>Safe systems of work</li>
      <li>Safe use, handling and storage – plant, structures, substances</li>
      <li>Adequate resources</li>
      <li>Information, training, instruction and supervision</li>
      <li>Continued monitoring</li>
    </ul>
  </div>
</section>

<footer class="site-footer">
  <div class="contact-row">
    <div class="contact-item">
      <svg width="16" height="16" viewBox="0 0 16 16"><path d="M3 1L6 4L4.5 6C5.5 8 8 10.5 10 11.5L12 10L15 13L13 15C7 14 2 9 1 3Z" fill="#6a6a6a"/></svg>
      t: +61 (0)2 9000 4172<br>f: +61 (0)2 9000 6385
    </div>
    <div class="contact-item">
      <svg width="18" height="14" viewBox="0 0 18 14"><rect x="1" y="1" width="16" height="12" fill="none" stroke="#6a6a6a" stroke-width="1.5"/><path d="M1 1L9 8L17 1" fill="none" stroke="#6a6a6a" stroke-width="1.5"/></svg>
      e: name@yourdomain.com
    </div>
    <div class="contact-item">
      <svg width="12" height="16" viewBox="0 0 12 16"><path d="M6 0C2.7 0 0 2.6 0 5.8C0 10 6 16 6 16S12 10 12 5.8C12 2.6 9.3 0 6 0Z" fill="#6a6a6a"/><circle cx="6" cy="5.8" r="2.2" fill="#1c1c1c"/></svg>
      Level 29, Harwell Tower<br>8 Kestin Square, Sydney, NSW 2000
    </div>
  </div>
  <div class="social"><span></span><span class="on"></span><span></span><span></span><span></span></div>
  <p class="copyright">© 2015. YOURSITE. ALL RIGHTS RESERVED</p>
</footer>
</body>
</html>
```